****Business Card Design for Quarrystone Development. Design based around attached logo/company name

I’m looking for business card design for my company Quarrystone Development Group,LLC. Design should be professional, sharp and minimal. Outside of the attached logos, greyscale colors for remainder of cards. My thoughts are two-sided card with attached logo on one side and my info on the other but open to one-sided as well with right design.
Target Market(s)
Real estate professionals including banks, private investors, property owners, developers, commercial tenants like Brewlantern, Grovika or Tanquist’s.
Industry/Entity Type
Commercial real estate development and investments.
Contact Information for Business Card
Name, title, email, phone #’s, web address and physical address
Font styles to use
Other font styles liked:
- Helvetica, Garamond, etc
Colors
Designer to choose only greyscale colors for use in the design.
Requirements
Must have
- Attached logo first or second options.
Nice to have
- Two sided card with logo on one side. Attached Logo/company name can be laid out any way that flows as long as it’s legible.name
Should not have
- No loud colors. ***Please do not include logo, I have removed the company design with a logo image.

```html
<!DOCTYPE html>
<html lang="en">
<head>
<meta charset="utf-8">
<title>Quarrystone Development Group, LLC — Business Card</title>
<link rel="stylesheet" href="https://fonts.googleapis.com/css2?family=Cormorant+Garamond:wght@500;700&family=Arimo:wght@400&display=swap">
<style>
  :root {
    --backdrop: #1b1b1c;
    --card: #232324;
    --card-edge: #2c2c2d;
    --ink-bright: #f1f1f1;
    --ink-soft: #d6d6d6;
    --ink-muted: #8a8b93;
    --rule: #6d6e75;
  }
  * { margin: 0; padding: 0; box-sizing: border-box; }
  html, body {
    width: 1200px; height: 900px; overflow: hidden;
    background: var(--backdrop);
  }
  .canvas {
    position: relative; width: 1200px; height: 900px;
  }
  .card {
    position: absolute; left: 280px; width: 640px; height: 366px;
    background: linear-gradient(160deg, var(--card-edge), var(--card));
    box-shadow: 0 18px 40px rgba(0,0,0,.55);
  }
  .card--front { top: 69px; }
  .card--back { top: 465px; }

  .front-wordmark {
    position: absolute; inset: 0;
    display: flex; align-items: center; justify-content: center;
    font-family: "Cormorant Garamond", Garamond, serif;
    font-weight: 500; font-size: 40px; letter-spacing: 6px;
    text-transform: uppercase; color: var(--ink-soft);
  }

  .company-name {
    position: absolute; left: 40px; top: 34px;
    font-family: "Cormorant Garamond", Garamond, serif;
    font-weight: 500; font-size: 26px; letter-spacing: 2px;
    text-transform: uppercase; color: var(--ink-bright);
    line-height: 1.1;
  }
  .phone {
    position: absolute; right: 40px; top: 120px;
    font-family: "Arimo", Helvetica, sans-serif; font-size: 17px;
    color: var(--ink-bright);
  }
  .label { color: var(--ink-muted); }

  .person {
    position: absolute; left: 40px; top: 168px;
  }
  .person-name {
    font-family: "Cormorant Garamond", Garamond, serif;
    font-weight: 700; font-size: 26px; letter-spacing: 4px;
    text-transform: uppercase; color: var(--ink-bright);
  }
  .person-title {
    font-family: "Arimo", Helvetica, sans-serif; font-size: 17px;
    color: var(--ink-soft); margin-top: 2px;
  }
  .divider {
    position: absolute; left: 40px; right: 40px; top: 246px;
    height: 1px; background: var(--rule);
  }
  .online, .address {
    position: absolute; top: 262px;
    font-family: "Arimo", Helvetica, sans-serif; font-size: 17px;
    line-height: 1.5; color: var(--ink-bright);
  }
  .online { left: 40px; }
  .address { right: 40px; text-align: left; }
</style>
</head>
<body>
<main class="canvas">
  <section class="card card--front" aria-label="Card front">
    <div class="front-wordmark">Quarrystone</div>
  </section>

  <section class="card card--back" aria-label="Card back">
    <div class="company-name">Quarrystone Development Group, LLC</div>
    <p class="phone"><span class="label">Cell:</span> (541) 555-0186</p>
    <div class="person">
      <h1 class="person-name">Daniel Hartwell</h1>
      <p class="person-title">Director</p>
    </div>
    <div class="divider"></div>
    <p class="online">
      <span class="label">Email:</span> info@quarrystonegroup.com<br>
      <span class="label">Web:</span> www.quarrystonegroup.com
    </p>
    <p class="address">
      <span class="label">Address:</span> 1187 Cedar Ridge<br>
      Lane Corvallis, OR 97330
    </p>
  </section>
</main>
</body>
</html>
```